Homeowners Insurance Provider Website

We are selling homeowners insurance policy / tenants Policy/Flood Insurance in USA in few states and planning expand nationally.

Our target audience are two folds: Customers (Buy policies) and Insurance Agents who wants to work with us to sell our policies to customers. But website should focus 80% on customers and 20% on agents. So, more customer focused user experience. Please note that there is no direct buy option for customers. They always go through insurance agents.

Customer focused, educational that makes buyer journey easy. We don’t want to come off as trying sell something as there is no direct sales involved from website.

Target Market(s)

Homeowners in USA and Insurance agent who sells these insurance.

Industry/Entity Type

Insurance

Number of Pages Required

4 page

Font styles to use
Other font styles liked:
• Open to suggestions

Colors

Designer to choose colors to be used in the design.

Requirements
Must have
• Three most important things: Trustworthy, Authentic, Simple
• Please use colors form logo and grays
• We like: www.hollowmere.com
• https://www.quillfenbrook.com/
• We need Agent Look up tool on home page similar to what is shown on example sites.
• Design:
• Home Page - Open to Ideas
• Insurance (Products) Landing Page - Info similar to: https://www.quillfenbrook.com/insurance/
• Agents Page - https://www.quillfenbrook.com/agents/
• Claims Page - Information similar to: https://www.quillfenbrook.com/claims-center/
• Site Navigation:
• Home
• Insurance
• Claims
• Agents
• About Us
• Contact Us
Nice to have
• Elegant, minimal and clean design that reflects trust and authenticity.
Should not have
• Slider or rotating images - prefer flat design. Not over powering design.

```html
<!DOCTYPE html>
<html lang="en">
<head>
<meta charset="utf-8">
<title>Hearthline Insurance Co.</title>
<link href="https://fonts.googleapis.com/css2?family=Poppins:wght@500;600;700&family=Open+Sans:wght@400;600&display=swap" rel="stylesheet">
<style>
:root{
  --navy:#233a84;
  --red:#d4232d;
  --ink:#2d2d33;
  --text:#6a6d75;
  --line:#dcdde2;
  --soft:#f1f2f5;
  --white:#ffffff;
}
*{box-sizing:border-box;margin:0;padding:0}
html,body{width:1200px;height:2612px;overflow:hidden}
body{font-family:"Open Sans",Arial,sans-serif;color:var(--text);background:var(--white);font-size:14px;line-height:1.6}
h1,h2,h3,.nav a,.brand{font-family:"Poppins",Arial,sans-serif}

.site-header{height:90px;display:flex;align-items:center;justify-content:space-between;padding:0 70px 0 90px;background:var(--white)}
.brand{display:flex;align-items:center;gap:10px;font-weight:600;font-size:16px;color:var(--navy);letter-spacing:.4px;white-space:nowrap}
.brand-mark{width:22px;height:22px;background:var(--red)}
.nav{display:flex;gap:34px}
.nav a{font-size:12px;font-weight:600;color:var(--ink);text-decoration:none;letter-spacing:.6px}
.nav a.active{color:var(--red)}

.hero{position:relative;height:590px;background:linear-gradient(90deg,#f3f4f6 0%,#eceef1 45%,#e2e4e8 100%);overflow:hidden}
.hero-photo{position:absolute;right:0;top:0;width:640px;height:590px;background:linear-gradient(135deg,#e9eaed 0%,#d8d2cc 45%,#b9b2ad 100%)}
.hero-copy{position:absolute;left:90px;top:205px;width:430px}
.hero-copy h1{font-size:46px;font-weight:700;color:var(--navy);line-height:1.1;letter-spacing:1px}
.hero-copy p{margin-top:22px;font-size:13px}
.hero-actions{display:flex;align-items:center;gap:26px;margin-top:30px}
.btn{display:inline-block;background:var(--red);color:var(--white);font-family:"Poppins",Arial,sans-serif;font-size:12px;font-weight:600;padding:9px 20px;letter-spacing:.5px}
.hero-phone{display:flex;align-items:center;gap:10px;font-family:"Poppins",Arial,sans-serif;font-size:26px;font-weight:600;color:var(--navy)}
.hero-curve{position:absolute;left:0;bottom:0;width:1200px;height:110px}

.welcome{height:680px;padding:90px 90px 0;text-align:center}
.section-title{font-size:32px;font-weight:600;color:var(--navy);letter-spacing:.5px}
.section-title .accent{color:var(--red)}
.welcome > p{max-width:900px;margin:22px auto 0;font-size:12px}
.features{display:grid;grid-template-columns:1fr 1fr;gap:60px 120px;margin-top:66px;padding:0 20px;text-align:left}
.feature{display:flex;gap:28px}
.feature svg{flex:none}
.feature h3{font-size:18px;font-weight:600;color:var(--navy)}
.feature p{font-size:12px;margin-top:6px}

.services{background:var(--soft);height:530px;padding:44px 90px 0;text-align:center}
.cards{display:grid;grid-template-columns:repeat(3,1fr);gap:34px;margin-top:32px}
.card{background:var(--white);box-shadow:0 2px 6px rgba(0,0,0,.08)}
.card-img{height:200px}
.card h3{font-size:19px;font-weight:600;color:var(--ink);margin-top:18px}
.card p{font-size:12px;padding:6px 30px 28px}

.testimonial{position:relative;height:310px;background:linear-gradient(90deg,var(--red) 0%,#a8303f 35%,#4a3b7e 65%,var(--navy) 100%);color:var(--white);text-align:center}
.quote-frame{position:absolute;left:200px;top:56px;width:800px;height:200px}
.quote-mark{position:absolute;left:570px;top:38px;font-family:"Poppins",Arial,sans-serif;font-size:90px;font-weight:700;line-height:1}
.testimonial p{position:absolute;left:210px;top:124px;width:780px;font-size:13px}
.testimonial cite{position:absolute;left:0;right:0;top:228px;font-style:normal;font-size:12px;font-weight:600}

.site-footer{height:340px;display:grid;grid-template-columns:542px 328px 1fr;padding:44px 90px 0}
.site-footer h2{font-size:20px;font-weight:600;color:var(--ink);letter-spacing:.4px;white-space:nowrap}
.quote-form{width:470px;display:grid;grid-template-columns:1fr 1fr;gap:14px;margin-top:26px}
.field{border:1px solid var(--line);height:38px;font-size:11px;padding:9px 12px}
.submit{background:var(--navy);color:var(--white);font-family:"Poppins",Arial,sans-serif;font-size:12px;font-weight:600;width:150px;height:36px;display:flex;align-items:center;justify-content:center;margin-top:14px}
.contact-list{list-style:none;margin-top:26px}
.contact-list li{display:flex;gap:12px;font-size:12px;margin-bottom:18px;align-items:flex-start}
.contact-list svg{flex:none;margin-top:2px}
.links{list-style:none;margin-top:26px}
.links li{font-size:12px;margin-bottom:10px;padding-left:16px;position:relative}
.links li::before{content:"";position:absolute;left:0;top:8px;width:5px;height:5px;background:var(--red)}

.bottom-bar{height:72px;border-top:1px solid var(--line);display:flex;align-items:center;justify-content:space-between;padding:0 70px 0 90px;font-size:11px}
.socials{display:flex;gap:8px;margin-left:180px}
.socials span{width:22px;height:22px;border:1px solid #9a9ca3;border-radius:50%}
.bottom-bar .brand{font-size:13px}
.bottom-bar .brand-mark{width:18px;height:18px}
</style>
</head>
<body>

<header class="site-header">
  <div class="brand"><span class="brand-mark"></span><span>HEARTHLINE INSURANCE CO.</span></div>
  <nav class="nav">
    <a class="active" href="#">HOME</a><a href="#">INSURANCE</a><a href="#">CLAIMS</a><a href="#">AGENTS</a><a href="#">ABOUT US</a><a href="#">CONTACT US</a>
  </nav>
</header>

<section class="hero">
  <div class="hero-photo" role="img" aria-label="Smiling woman working on a laptop in a bright office"></div>
  <div class="hero-copy">
    <h1>HOMEOWNERS<br>INSURANCE</h1>
    <p>Protect the place you call home with clear coverage, trusted local agents and simple answers at every step of your journey.</p>
    <div class="hero-actions">
      <span class="btn">READ MORE</span>
      <span class="hero-phone">
        <svg width="22" height="22" viewBox="0 0 24 24"><path fill="#233a84" d="M6.6 10.8a15 15 0 0 0 6.6 6.6l2.2-2.2a1 1 0 0 1 1-.25 11.4 11.4 0 0 0 3.6.57 1 1 0 0 1 1 1V20a1 1 0 0 1-1 1A17 17 0 0 1 3 4a1 1 0 0 1 1-1h3.5a1 1 0 0 1 1 1c0 1.25.2 2.45.57 3.6a1 1 0 0 1-.25 1z"/></svg>
        800-555-0142
      </span>
    </div>
  </div>
  <svg class="hero-curve" viewBox="0 0 1200 110" preserveAspectRatio="none">
    <path d="M0 110 L0 70 Q600 -10 1200 70 L1200 110 Z" fill="#ffffff"/>
    <path d="M0 66 Q600 -14 1200 66" fill="none" stroke="#233a84" stroke-width="6"/>
    <path d="M0 58 Q600 -22 1200 58" fill="none" stroke="#d4232d" stroke-width="3"/>
  </svg>
</section>

<section class="welcome">
  <h2 class="section-title">WELCOME TO <span class="accent">HEARTHLINE</span> INSURANCE</h2>
  <p>We help families across the country find the right protection for their homes, rentals and belongings. Our network of independent agents guides you through every option, explains coverage in plain words and stays by your side when you need to file a claim. Learn how policies work, compare choices with confidence and connect with an agent near you today.</p>
  <div class="features">
    <div class="feature">
      <svg width="62" height="70" viewBox="0 0 62 70"><path d="M31 3 L58 13 V34 C58 52 44 62 31 67 C18 62 4 52 4 34 V13 Z" fill="none" stroke="#233a84" stroke-width="3"/><path d="M19 36 L31 26 L43 36 M23 33 V46 H39 V33" fill="none" stroke="#d4232d" stroke-width="3"/></svg>
      <div><h3>Homeowners</h3><p>Coverage for your dwelling, personal property and liability, with options designed around the way your family lives.</p></div>
    </div>
    <div class="feature">
      <svg width="62" height="70" viewBox="0 0 62 70"><path d="M31 3 L58 13 V34 C58 52 44 62 31 67 C18 62 4 52 4 34 V13 Z" fill="none" stroke="#233a84" stroke-width="3"/><path d="M20 26 H32 L44 38 L34 48 L20 36 Z" fill="none" stroke="#d4232d" stroke-width="3"/><circle cx="26" cy="31" r="2" fill="#d4232d"/></svg>
      <div><h3>Renters/Condo</h3><p>Protect your belongings and personal liability whether you rent an apartment or own a condo unit.</p></div>
    </div>
    <div class="feature">
      <svg width="62" height="70" viewBox="0 0 62 70"><path d="M31 3 L58 13 V34 C58 52 44 62 31 67 C18 62 4 52 4 34 V13 Z" fill="none" stroke="#233a84" stroke-width="3"/><path d="M19 36 L31 26 L43 36 M23 33 V46 H39 V33" fill="none" stroke="#d4232d" stroke-width="3"/><path d="M31 44 C27 41 28 37 31 34 C34 37 35 41 31 44 Z" fill="#d4232d"/></svg>
      <div><h3>Dwelling Fire</h3><p>Affordable protection for rental or seasonal properties against fire and other named perils you choose.</p></div>
    </div>
    <div class="feature">
      <svg width="62" height="70" viewBox="0 0 62 70"><path d="M31 3 L58 13 V34 C58 52 44 62 31 67 C18 62 4 52 4 34 V13 Z" fill="none" stroke="#233a84" stroke-width="3"/><path d="M31 50 C24 41 22 37 22 33 A9 9 0 0 1 40 33 C40 37 38 41 31 50 Z" fill="none" stroke="#d4232d" stroke-width="3"/><circle cx="31" cy="33" r="3" fill="#d4232d"/></svg>
      <div><h3>Agent Locator Tool</h3><p>Enter your ZIP code to find a trusted local agent who can answer questions and help you get covered.</p></div>
    </div>
  </div>
</section>

<section class="services">
  <h2 class="section-title">WHAT WE DO</h2>
  <div class="cards">
    <article class="card">
      <div class="card-img" role="img" aria-label="Hands sheltering paper cut-out family figures" style="background:linear-gradient(135deg,#3a3d47,#8f939c)"></div>
      <h3>Insurance</h3>
      <p>Explore policies that fit your home and budget, explained simply so you know what you are buying.</p>
    </article>
    <article class="card">
      <div class="card-img" role="img" aria-label="Family reviewing documents at home" style="background:linear-gradient(135deg,#c9b59a,#6f7f8e)"></div>
      <h3>Claims</h3>
      <p>Report a loss, track progress and get support from a team that moves quickly when it matters.</p>
    </article>
    <article class="card">
      <div class="card-img" role="img" aria-label="Agent holding a red umbrella" style="background:linear-gradient(135deg,#e6e7ea,#c7434a)"></div>
      <h3>Agents</h3>
      <p>Join our growing network of agents and offer customers reliable coverage backed by real service.</p>
    </article>
  </div>
</section>

<section class="testimonial">
  <svg class="quote-frame" viewBox="0 0 800 200"><path d="M340 2 H2 V198 H60 M740 198 H798 V2 H460" fill="none" stroke="#ffffff" stroke-width="2"/></svg>
  <div class="quote-mark">&rdquo;</div>
  <p>My agent walked me through every option and helped me understand exactly what my policy covers. When a storm damaged our roof, the claim was handled quickly and fairly. I finally feel confident that our home and family are protected the right way.</p>
  <cite>Dana Whitfield - Hearthline Insurance</cite>
</section>

<footer class="site-footer">
  <div>
    <h2>GET A QUICK NOW!</h2>
    <div class="quote-form">
      <div class="field">Your Name</div>
      <div class="field">Your E-Mail</div>
      <div class="field">Your Phone</div>
      <div class="field">Message</div>
    </div>
    <div class="submit">SUBMIT</div>
  </div>
  <div>
    <h2>CONTACT US</h2>
    <ul class="contact-list">
      <li><svg width="14" height="16" viewBox="0 0 24 24"><path fill="#6a6d75" d="M12 2a7 7 0 0 0-7 7c0 5 7 13 7 13s7-8 7-13a7 7 0 0 0-7-7zm0 9.5A2.5 2.5 0 1 1 12 6.5a2.5 2.5 0 0 1 0 5z"/></svg><span>Hearthline Insurance P.O. Box 1420<br>Fairbrook, CT 06118</span></li>
      <li><svg width="14" height="16" viewBox="0 0 24 24"><path fill="#6a6d75" d="M6.6 10.8a15 15 0 0 0 6.6 6.6l2.2-2.2a1 1 0 0 1 1-.25 11.4 11.4 0 0 0 3.6.57 1 1 0 0 1 1 1V20a1 1 0 0 1-1 1A17 17 0 0 1 3 4a1 1 0 0 1 1-1h3.5a1 1 0 0 1 1 1c0 1.25.2 2.45.57 3.6a1 1 0 0 1-.25 1z"/></svg><span>Phone: 1 800 555 0142<br>Fax: 1 800 555 0143</span></li>
      <li><svg width="14" height="16" viewBox="0 0 24 24"><path fill="#6a6d75" d="M3 5h18v14H3z M3 5l9 7 9-7" stroke="#ffffff" stroke-width="1.5"/></svg><span>Email: info@hearthlineinsure.com</span></li>
    </ul>
  </div>
  <div>
    <h2>QUICK LINKS</h2>
    <ul class="links"><li>Home</li><li>Insurance</li><li>Claims</li><li>Agents</li><li>About Us</li><li>Contact Us</li></ul>
  </div>
</footer>

<div class="bottom-bar">
  <span>&copy;2018 Hearthline Insurance. All Rights Reserved</span>
  <div class="socials"><span></span><span></span><span></span><span></span></div>
  <div class="brand"><span class="brand-mark"></span><span>HEARTHLINE INSURANCE CO.</span></div>
</div>

</body>
</html>
```